Business Card Design for The Lending Nest Inc.

We need a business card design for our mortgage company: "The Lending Nest Inc."

Need to have Social Media Account on there as a possibility

```html
<!DOCTYPE html>
<html lang="en">
<head>
<meta charset="utf-8">
<title>The Lending Nest Inc. – Business Card</title>
<link href="https://fonts.googleapis.com/css2?family=Questrial&family=Open+Sans:wght@400;600&family=Roboto+Condensed:wght@400&family=Montserrat:wght@700&display=swap" rel="stylesheet">
<style>
  :root{
    --page:#ffffff;
    --card:#1d1d1d;
    --card-edge:#141414;
    --band-grey:#434343;
    --band-red:#7c1619;
    --band-blue:#0e5aa6;
    --brand-blue:#1560ae;
    --link-blue:#3a8fd6;
    --icon-blue:#1d8ff0;
    --stitch:#9a9a9a;
    --text:#ffffff;
  }
  *{margin:0;padding:0;box-sizing:border-box}
  html,body{width:1200px;height:1200px;overflow:hidden;background:var(--page)}
  .card{
    position:absolute;left:107px;width:900px;height:540px;overflow:hidden;
    background:radial-gradient(ellipse at 50% 45%, #242424 0%, var(--card) 55%, var(--card-edge) 100%);
  }
  .card--front{top:62px}
  .card--back{top:647px}

  .stripes{position:absolute;left:0;top:0;width:527px;height:100%}
  .band{
    position:absolute;left:0;width:527px;height:56px;
    display:flex;align-items:center;padding-left:82px;
    font-family:"Questrial",sans-serif;font-size:19px;color:var(--text);
    box-shadow:0 2px 6px rgba(0,0,0,.5);
  }
  .band--grey{background:var(--band-grey)}
  .band--red{background:var(--band-red)}
  .band .name{font-family:"Montserrat",sans-serif;font-weight:700;font-size:18px;margin-right:36px}
  .band .gap{margin-right:34px}
  .stitch{position:absolute;left:0;height:0;border-top:2px dashed var(--stitch);opacity:.75}
  .stripes .stitch{width:527px}

  .brand-mark{position:absolute;display:flex;align-items:center;
    font-family:"Open Sans",sans-serif;font-weight:600;color:var(--brand-blue)}
  .brand-mark .dot{border-radius:50%;border:3px solid var(--brand-blue);flex:none}
  .card--front .brand-mark{left:560px;top:84px;font-size:23px;gap:12px}
  .card--front .brand-mark .dot{width:54px;height:54px}
  .company{position:absolute;left:551px;top:160px;font-family:"Open Sans",sans-serif;
    font-size:37px;color:var(--text)}
  .social{position:absolute;left:560px;list-style:none}
  .social li{position:absolute;left:0;display:flex;align-items:center;white-space:nowrap}
  .social .icon{width:36px;height:36px;border-radius:50%;background:var(--icon-blue)}
  .social .handle{font-family:"Roboto Condensed",sans-serif;font-size:29px;color:var(--link-blue);margin-left:26px}

  .card--back .brand-mark{left:175px;top:148px;font-size:50px;gap:22px}
  .card--back .brand-mark .dot{width:120px;height:120px;border-width:5px}
  .web-band{position:absolute;left:0;top:387px;width:900px;height:56px;background:var(--band-blue);
    display:flex;align-items:center;justify-content:center;
    font-family:"Questrial",sans-serif;font-size:25px;color:var(--text);letter-spacing:.5px}
  .card--back .stitch{width:900px}
</style>
</head>
<body>
  <section class="card card--front">
    <div class="stripes">
      <span class="stitch" style="top:94px"></span>
      <div class="band band--grey" style="top:102px"><span class="name">RAYAN MALIK</span><span>GRAPHIC DESIGER</span></div>
      <span class="stitch" style="top:164px"></span>
      <div class="band band--red" style="top:170px"><span class="gap">00-410-555-128</span><span>00-410-555-396</span></div>
      <span class="stitch" style="top:233px"></span>
      <div class="band band--grey" style="top:240px">www.lendingnestinc.com</div>
      <span class="stitch" style="top:303px"></span>
      <div class="band band--red" style="top:310px">hello@lendingnestinc.com</div>
      <span class="stitch" style="top:374px"></span>
      <div class="band band--grey" style="top:380px">Office 22 Cedar Road Dubai UAE</div>
      <span class="stitch" style="top:443px"></span>
    </div>

    <div class="brand-mark"><span class="dot"></span><span>The Lending Nest Inc.</span></div>
    <div class="company">Lending Nest Inc</div>
    <ul class="social">
      <li style="top:218px"><span class="icon"></span><span class="handle">/YOUR PROFILE</span></li>
      <li style="top:274px"><span class="icon"></span><span class="handle">/YOUR PAGE</span></li>
      <li style="top:330px"><span class="icon"></span></li>
    </ul>
  </section>

  <section class="card card--back">
    <div class="brand-mark"><span class="dot"></span><span>The Lending Nest Inc.</span></div>
    <span class="stitch" style="top:381px"></span>
    <div class="web-band">www.lendingnestinc.com</div>
    <span class="stitch" style="top:450px"></span>
  </section>
</body>
</html>
```